We are a building company that build new homes and units we are looking for something fresh and looks good my company name is
Lark Building Co Pty Ltd

Industry/Entity Type

Building

Contact Information for Business Card

Name Marco Ellis-Dunford
Tittle: Director
Address 14 Corrin St. Pelham Vale Vic 3179
Ph: 03 9582 4063
Mobile : 0400 362 918

www.larkbuildingco.com.au
Email: sales@larkbuildingco.com.au

```html
<!DOCTYPE html>
<html lang="en">
<head>
<meta charset="utf-8">
<title>Lark Building Co Pty Ltd – Business Card</title>
<link href="https://fonts.googleapis.com/css2?family=Arimo:wght@400;700&display=swap" rel="stylesheet">
<style>
  :root {
    --page-bg: #e9e7e3;
    --card-bg: #ffffff;
    --brand-green: #4cbf3f;
    --brand-green-dark: #3aa82f;
    --ink-grey: #6b6b6b;
    --rule-grey: #8a8a8a;
    --shadow: rgba(0,0,0,0.18);
  }
  html, body {
    margin: 0;
    padding: 0;
    width: 1200px;
    height: 885px;
    overflow: hidden;
    background: var(--page-bg);
    font-family: "Arimo", Arial, sans-serif;
  }
  .canvas {
    position: relative;
    width: 1200px;
    height: 885px;
  }
  .card {
    position: absolute;
    background: var(--card-bg);
    box-shadow: 0 10px 28px var(--shadow);
    overflow: hidden;
  }

  /* Front (portrait) */
  .card-front {
    left: 110px;
    top: 120px;
    width: 380px;
    height: 620px;
  }
  .wordmark {
    display: flex;
    align-items: center;
    justify-content: center;
    gap: 10px;
    color: var(--ink-grey);
    font-weight: 400;
    letter-spacing: 0.06em;
    text-transform: uppercase;
  }
  .wordmark-square {
    width: 14px;
    height: 14px;
    background: var(--brand-green);
    flex: none;
  }
  .front-brand {
    position: absolute;
    top: 70px;
    left: 30px;
    right: 30px;
    text-align: center;
  }
  .front-brand .wordmark { font-size: 21px; }
  .brand-rule {
    height: 1px;
    background: var(--rule-grey);
    margin: 16px auto 0;
    width: 86%;
  }
  .contact-person {
    position: absolute;
    top: 215px;
    left: 0;
    right: 0;
    text-align: center;
  }
  .person-name {
    color: var(--brand-green);
    font-weight: 700;
    font-size: 29px;
    margin: 0;
  }
  .person-mobile {
    color: var(--ink-grey);
    font-weight: 700;
    font-size: 23px;
    margin: 6px 0 0;
  }
  .contact-office {
    position: absolute;
    top: 385px;
    left: 0;
    right: 0;
    text-align: center;
  }
  .office-phone {
    color: var(--ink-grey);
    font-weight: 700;
    font-size: 26px;
    margin: 0;
  }
  .office-email {
    color: var(--ink-grey);
    font-size: 17px;
    margin: 18px 0 0;
  }
  .web-band {
    position: absolute;
    left: 0;
    right: 0;
    bottom: 0;
    height: 92px;
    background: linear-gradient(180deg, var(--brand-green) 0%, var(--brand-green-dark) 100%);
    display: flex;
    align-items: center;
    justify-content: center;
  }
  .web-address {
    color: #ffffff;
    font-size: 20px;
    margin: 0;
    letter-spacing: 0.01em;
  }

  /* Back (landscape) */
  .card-back {
    left: 540px;
    top: 255px;
    width: 620px;
    height: 380px;
    display: flex;
    flex-direction: column;
    align-items: center;
    justify-content: center;
  }
  .card-back .wordmark { font-size: 34px; gap: 16px; }
  .card-back .wordmark-square { width: 22px; height: 22px; }
  .card-back .brand-rule { width: 72%; margin-top: 26px; }
</style>
</head>
<body>
<main class="canvas">
  <section class="card card-front" aria-label="Business card front">
    <div class="front-brand">
      <div class="wordmark"><span class="wordmark-square"></span>Lark Building Co Pty Ltd</div>
      <div class="brand-rule"></div>
    </div>
    <div class="contact-person">
      <p class="person-name">Marco Ellis-Dunford</p>
      <p class="person-mobile">0400 362 918</p>
    </div>
    <div class="contact-office">
      <p class="office-phone">03 9582 4063</p>
      <p class="office-email">sales@larkbuildingco.com.au</p>
    </div>
    <div class="web-band">
      <p class="web-address">www.larkbuildingco.com.au</p>
    </div>
  </section>

  <section class="card card-back" aria-label="Business card back">
    <div class="wordmark"><span class="wordmark-square"></span>Lark Building Co Pty Ltd</div>
    <div class="brand-rule"></div>
  </section>
</main>
</body>
</html>
```